Looking for a dynamic business card for a pizzeria.

A business card with our food, logo, and space for name, title, email, website, phone. The card should convey quality, unique, amazing. On the front, I envision food photo or photos with the owners names and contact information. On the back, more food with locations, website, facebook, twitter, instagram icons. It should look polished, not cartoonish, or plain.
Target Market(s)
upscale, local food buyers, 30-50 years in age.
Industry/Entity Type
Restaurant
Contact Information for Business Card
Business Name: Bru'nettix, LLC
Website: www.brunettix.com
Back:
2 locations: (can list on the back of card)
1. Harborview
4087 Corlan Avenue
Larkston, WA 98412
360-481-5067
2. Cedar Ridge
7315 Wendmere Road
Larkston, WA 98417
360-293-8840
front:
EDITABLE space for
Business name
Person's Name
title
2nd title
Email address
cell-phone number
Requirements
Must have
- logo
- my food photo or photos (no watermarks showing)
- locations on back
- Person contact information on front
- full bleed

```html
<!DOCTYPE html>
<html lang="en">
<head>
<meta charset="utf-8">
<title>Brunettix Business Card</title>
<link href="https://fonts.googleapis.com/css2?family=Arimo:wght@400;700&display=swap" rel="stylesheet">
<style>
  :root {
    --green: #2e6a32;
    --green-text: #3f7d3a;
    --white: #ffffff;
    --ink: #1c1c1c;
    --page: #ecebe7;
  }
  * { margin: 0; padding: 0; box-sizing: border-box; }
  html, body { width: 1200px; height: 950px; overflow: hidden; }
  body {
    background: var(--page);
    font-family: "Arimo", Arial, sans-serif;
    position: relative;
  }
  .card {
    position: absolute;
    left: 230px;
    width: 740px;
    height: 423px;
    overflow: hidden;
    box-shadow: 0 6px 20px rgba(0,0,0,.18);
  }
  /* Front */
  .card-front { top: 32px; background: var(--green); }
  .social { position: absolute; top: 24px; right: 28px; display: flex; gap: 10px; }
  .social span { width: 18px; height: 18px; border-radius: 50%; background: var(--white); display: block; }
  .front-brand {
    position: absolute; top: 92px; left: 0; right: 0; text-align: center;
    color: var(--white); font-size: 48px; font-weight: 400; letter-spacing: 3px;
  }
  .food-row { position: absolute; left: 60px; right: 60px; top: 200px; height: 180px; }
  .food-photo { position: absolute; width: 170px; height: 150px; }
  .food-photo.one { left: 0; top: 30px; }
  .food-photo.two { left: 225px; top: 0; }
  .food-photo.three { left: 450px; top: -20px; }
  /* Back */
  .card-back { top: 495px; background: var(--white); }
  .back-brand {
    position: absolute; top: 50px; right: 60px;
    color: var(--green); font-size: 42px; font-weight: 400; letter-spacing: 3px;
  }
  .band { position: absolute; left: 0; right: 0; top: 150px; height: 52px; background: var(--green); }
  .name-block {
    position: absolute; left: 0; top: 150px; width: 240px; height: 118px;
    background: var(--green); color: var(--white);
    padding: 62px 0 0 32px;
  }
  .person-name { font-size: 20px; font-weight: 700; letter-spacing: .5px; }
  .person-title { font-size: 13px; margin-top: 4px; }
  .location { position: absolute; font-size: 15px; line-height: 1.35; color: var(--ink); font-style: normal; }
  .location .place, .location .label { color: var(--green-text); }
  .location.harborview { left: 32px; top: 292px; }
  .location.cedar-ridge { left: 262px; top: 222px; }
  .contact { position: absolute; left: 490px; top: 222px; list-style: none; font-size: 14px; color: var(--ink); }
  .contact li { display: flex; align-items: center; gap: 10px; margin-bottom: 7px; }
  .contact svg { width: 16px; height: 16px; fill: var(--green); flex: none; }
</style>
</head>
<body>

<section class="card card-front" aria-label="Card front">
  <div class="social" aria-hidden="true"><span></span><span></span></div>
  <div class="front-brand">BRUNETTIX</div>
  <div class="food-row">
    <svg class="food-photo one" viewBox="0 0 170 150" role="img" aria-label="Photo of a grilled panini sandwich">
      <defs><linearGradient id="g1" x1="0" y1="0" x2="1" y2="1"><stop offset="0" stop-color="#d9a35e"/><stop offset="1" stop-color="#6f8a3c"/></linearGradient></defs>
      <polygon points="85,0 170,45 170,150 0,150 0,45" fill="url(#g1)"/>
    </svg>
    <svg class="food-photo two" viewBox="0 0 170 150" role="img" aria-label="Photo of a flatbread wrap with steak and onions">
      <defs><linearGradient id="g2" x1="0" y1="0" x2="1" y2="1"><stop offset="0" stop-color="#e4cf9c"/><stop offset="1" stop-color="#6b3b2c"/></linearGradient></defs>
      <polygon points="85,0 170,45 170,150 0,150 0,45" fill="url(#g2)"/>
    </svg>
    <svg class="food-photo three" viewBox="0 0 170 150" role="img" aria-label="Photo of hands stretching pizza dough">
      <defs><linearGradient id="g3" x1="0" y1="0" x2="1" y2="1"><stop offset="0" stop-color="#c9a98a"/><stop offset="1" stop-color="#e9dac4"/></linearGradient></defs>
      <polygon points="85,0 170,45 170,150 0,150 0,45" fill="url(#g3)"/>
    </svg>
  </div>
</section>

<section class="card card-back" aria-label="Card back">
  <div class="back-brand">BRUNETTIX</div>
  <div class="band"></div>
  <div class="name-block">
    <p class="person-name">ELENA VARSI</p>
    <p class="person-title">President</p>
  </div>
  <address class="location harborview">
    <span class="place">Harborview</span><br>
    4087 Corlan Avenue<br>
    Larkston, WA 98412<br>
    <span class="label">Phone:</span>360-481-5067
  </address>
  <address class="location cedar-ridge">
    <span class="place">Cedar Ridge</span><br>
    7315 Wendmere Road<br>
    Larkston, WA 98417<br>
    <span class="label">Phone:</span>360-293-8840
  </address>
  <ul class="contact">
    <li><svg viewBox="0 0 16 16" aria-hidden="true"><path d="M4 1h8a1 1 0 0 1 1 1v12a1 1 0 0 1-1 1H4a1 1 0 0 1-1-1V2a1 1 0 0 1 1-1zm1 2v9h6V3z"/></svg>689 514 7302</li>
    <li><svg viewBox="0 0 16 16" aria-hidden="true"><path d="M1 3h14v10H1zm1.5 1.2L8 8.4l5.5-4.2z"/></svg>name@brunettix.com</li>
    <li><svg viewBox="0 0 16 16" aria-hidden="true"><circle cx="8" cy="8" r="7"/><path d="M1 8h14M8 1c3 3 3 11 0 14M8 1c-3 3-3 11 0 14" stroke="#fff" stroke-width="1.1" fill="none"/></svg>www.brunettix.com</li>
  </ul>
</section>

</body>
</html>
```